Home Loan Introducer needs logo/business cards

We need a simple but classy logo for business cards and flyers. The business is a home loan referral business that is called an Introducer. The business name is "The Harborline".
I was thinking very simple and straight to the point on the front with "Home Loans" the only thing on the front with a nice background colour/s.
Then on the back, "The Harborline"
and "Quality Customer Service"
and "Email, text or call welcome"
and then my name, email address and phone number.
Updates
Thank you for all the designs :-)
Target Market(s)
Home buyers.
Home owners.
Investors.
Industry/Entity Type
Loan
Look and feel

```html
<!DOCTYPE html>
<html lang="en">
<head>
<meta charset="utf-8">
<title>The Harborline – Business Cards</title>
<link rel="stylesheet" href="https://fonts.googleapis.com/css2?family=Exo+2:wght@400;600;800&display=swap">
<style>
  :root {
    --stage: #e9e6e1;
    --card-dark: #222222;
    --accent-orange: #fbb034;
    --accent-blue: #1a6fc9;
    --ink-light: #ffffff;
    --ink-dark: #1b1b1b;
    --house-shade: #2c2c2c;
  }
  * { box-sizing: border-box; margin: 0; padding: 0; }
  html, body {
    width: 1200px; height: 750px; overflow: hidden;
    background: var(--stage);
    font-family: "Exo 2", sans-serif;
  }
  .stage { position: relative; width: 1200px; height: 750px; }

  .card {
    position: absolute;
    width: 490px; height: 300px;
    background: var(--card-dark);
    border-radius: 2px;
    box-shadow: 0 8px 22px rgba(0,0,0,.25);
    overflow: hidden;
  }

  /* Contact side */
  .card--contact { left: 150px; top: 70px; }
  .card--contact .band {
    position: absolute; left: 0; right: 0; bottom: 0; height: 98px;
    background: var(--accent-orange);
  }
  .brand {
    position: absolute; left: 0; right: 0; top: 118px;
    display: flex; justify-content: center; align-items: center; gap: 10px;
  }
  .brand__mark { width: 18px; height: 18px; background: var(--accent-orange); }
  .brand__name {
    color: var(--accent-orange); font-weight: 600; font-size: 22px;
    letter-spacing: .5px; text-transform: uppercase; line-height: 26px;
  }
  .perks {
    position: absolute; left: 178px; top: 155px; list-style: none;
    color: var(--accent-blue); font-size: 14px; line-height: 19px;
  }
  .perks li { display: flex; align-items: center; gap: 4px; }
  .perks svg { width: 12px; height: 12px; flex: none; }
  .person {
    position: absolute; left: 0; right: 0; top: 214px; text-align: center;
  }
  .person__name { color: var(--ink-dark); font-weight: 600; font-size: 19px; line-height: 23px; }
  .person__rule {
    width: 150px; height: 2px; background: var(--ink-light); margin: 2px auto 4px;
  }
  .person__line { font-size: 10px; color: var(--ink-light); line-height: 13px; }
  .person__line span { color: var(--accent-blue); }

  /* Headline side */
  .card--headline { left: 560px; top: 270px; width: 500px; height: 310px; }
  .skyline {
    position: absolute; left: 118px; top: 40px; width: 270px; height: 90px;
    background: linear-gradient(var(--house-shade), var(--card-dark));
  }
  .headline {
    position: absolute; left: 48px; right: 48px; top: 128px; height: 104px;
    background: var(--accent-orange); border-radius: 8px;
    display: flex; align-items: center; justify-content: center; gap: 14px;
    font-weight: 800; font-size: 60px; letter-spacing: 1px;
  }
  .headline__home { color: var(--ink-light); }
  .headline__loan { color: var(--accent-blue); }
</style>
</head>
<body>
<main class="stage">
  <section class="card card--contact">
    <div class="band"></div>
    <div class="brand">
      <span class="brand__mark"></span>
      <span class="brand__name">The Harborline</span>
    </div>
    <ul class="perks">
      <li><svg viewBox="0 0 12 12"><path d="M1 6l3 4 7-9" fill="none" stroke="#fff" stroke-width="2"/></svg>Quality Customer Service</li>
      <li><svg viewBox="0 0 12 12"><path d="M1 6l3 4 7-9" fill="none" stroke="#fff" stroke-width="2"/></svg>Email, text or call welcome</li>
    </ul>
    <div class="person">
      <p class="person__name">Owen Hale</p>
      <div class="person__rule"></div>
      <p class="person__line">Phone: <span>+6391 555 0187</span></p>
      <p class="person__line">Email: <span>owen@harborline.net</span></p>
    </div>
  </section>

  <section class="card card--headline">
    <div class="skyline" role="img" aria-label="Faint row of three house silhouettes"></div>
    <h1 class="headline">
      <span class="headline__home">HOME</span>
      <span class="headline__loan">LOAN</span>
    </h1>
  </section>
</main>
</body>
</html>
```